Business card design for new eCommerce site focusing on integrity and strong businsess tactics

We need a business card that will stand out and be memorable. Something with color that matches our company logo colors. Think high end version of Pactivo. There are 2 logos provided. The parent company is called Amber Ledge Partners and we are presenting a new and very exciting eCommerce site called BrightHarborTrade.example.

Target Market(s)

Our target markets are in the Activities, Food and Beverage, Health and Beauty

Industry/Entity Type

Marketing

Contact Information for Business Card

We have 4 members that need cards...I will provide all info to the winner of the design contest
Business Address is
4870 West 63rd Avenue, Suite C207
Phoenix AZ 85731

Font styles to use
Serif
Sans Serif

Colors

Designer to choose colors to be used in the design.

Requirements
Must have
• The card must be memorable...should be unique in design but must exude integrity and be playful .
• I have provided several colors or our parent company...please feel free to use which ever
Nice to have
• I will leave this up to you. Feel free to use other images of your choosing that wraps around our client.....Activities, Dining, Health, Beauty
Should not have
• just dont be boring

```html
<!DOCTYPE html>
<html lang="en">
<head>
<meta charset="utf-8">
<title>BrightHarborTrade.example – Business Card</title>
<link rel="stylesheet" href="https://fonts.googleapis.com/css2?family=Questrial&family=Roboto:wght@400;500&display=swap">
<style>
  :root {
    --backdrop: #2b2b2b;
    --card-white: #f7f7f5;
    --brand-blue: #2e7db3;
    --brand-green: #8cc63f;
    --ink-grey: #5b5b5b;
    --text-white: #ffffff;
  }
  * { box-sizing: border-box; margin: 0; padding: 0; }
  html, body {
    width: 1200px; height: 960px; overflow: hidden;
    background: var(--backdrop);
  }
  .canvas { position: relative; width: 1200px; height: 960px; }

  .card {
    position: absolute;
    width: 600px; height: 342px;
    border-radius: 18px;
    background: var(--card-white);
    overflow: hidden;
  }
  .card-front { left: 320px; top: 100px; }
  .card-back  { left: 320px; top: 493px; }

  /* Front */
  .front-brand {
    position: absolute; left: 100px; top: 152px;
    display: flex; align-items: center; gap: 14px;
  }
  .brand-dot {
    width: 34px; height: 34px; border-radius: 50%;
    background: var(--brand-green); flex: none;
  }
  .brand-name {
    font-family: "Questrial", sans-serif;
    font-size: 31px; line-height: 1;
    color: var(--brand-blue);
  }
  .front-tagline {
    position: absolute; left: 148px; top: 198px;
    font-family: "Questrial", sans-serif;
    font-size: 15px; letter-spacing: 1.4px;
    color: var(--ink-grey);
  }

  /* Back */
  .back-panel { position: absolute; inset: 0; }
  .back-brand {
    position: absolute; right: 40px; top: 50px;
    text-align: right;
  }
  .back-brand .brand-name {
    font-size: 21px; color: var(--brand-green);
  }
  .back-tagline {
    margin-top: 6px;
    font-family: "Questrial", sans-serif;
    font-size: 11.5px; letter-spacing: 1px;
    color: var(--text-white);
  }
  .contact {
    position: absolute; right: 40px; top: 137px;
    text-align: right;
    font-family: "Roboto", sans-serif;
    color: var(--text-white);
  }
  .contact-name {
    font-weight: 500; font-size: 22px; letter-spacing: 0.5px;
    color: var(--brand-green); line-height: 1.1;
  }
  .contact-title {
    font-weight: 500; font-size: 14px; margin-top: 3px;
  }
  .contact-address {
    font-size: 14px; line-height: 18px; margin-top: 10px;
  }
  .contact-lines { list-style: none; margin-top: 10px; }
  .contact-lines li {
    font-size: 14px; line-height: 19.5px;
    display: flex; justify-content: flex-end; align-items: center; gap: 6px;
  }
  .contact-lines svg { width: 13px; height: 13px; fill: var(--brand-green); flex: none; }
  .contact-address { margin-right: 19px; }
  .contact-name, .contact-title { margin-right: 0; }
</style>
</head>
<body>
<main class="canvas">

  <section class="card card-front" aria-label="Card front">
    <div class="front-brand">
      <span class="brand-dot"></span>
      <span class="brand-name">BrightHarborTrade.example</span>
    </div>
    <p class="front-tagline">Activities-Dining-Health-Beauty</p>
  </section>

  <section class="card card-back" aria-label="Card back">
    <svg class="back-panel" viewBox="0 0 600 342" width="600" height="342" aria-hidden="true">
      <path d="M200,0 C245,40 300,85 282,135 C262,192 172,238 192,342 L600,342 L600,0 Z" fill="var(--brand-blue)"/>
    </svg>

    <div class="back-brand">
      <span class="brand-name">BrightHarborTrade.example</span>
      <p class="back-tagline">Activities-Dining-Health-Beauty</p>
    </div>

    <div class="contact">
      <p class="contact-name">DANA REYES</p>
      <p class="contact-title">CEO/FOUNDER</p>
      <p class="contact-address">4870 West 63rd Avenue<br>Suite C207, Phoenix AZ 85731</p>
      <ul class="contact-lines">
        <li>555 014 2738
          <svg viewBox="0 0 16 16"><path d="M3.6 1.2l2.4 2.9-1.3 1.9c.9 2 2.4 3.5 4.4 4.4l1.9-1.3 2.9 2.4-1.3 2.4C7 13.8 2.2 9 1.2 2.5z"/></svg>
        </li>
        <li>555 019 6420
          <svg viewBox="0 0 16 16"><path d="M4.5 0h7A1.5 1.5 0 0 1 13 1.5v13a1.5 1.5 0 0 1-1.5 1.5h-7A1.5 1.5 0 0 1 3 14.5v-13A1.5 1.5 0 0 1 4.5 0zM5 2v10h6V2zm3 11a1 1 0 1 0 0 2 1 1 0 0 0 0-2z"/></svg>
        </li>
        <li>dana@brightharbortrade.example
          <svg viewBox="0 0 16 16"><path d="M1 3h14v1.2L8 9 1 4.2zM1 5.8l7 4.8 7-4.8V13H1z"/></svg>
        </li>
        <li>www.brightharbortrade.example
          <svg viewBox="0 0 16 16"><path d="M8 1a7 7 0 1 0 0 14A7 7 0 0 0 8 1zm0 1.5c.9 0 1.9 1.8 2.2 4.5H5.8C6.1 4.3 7.1 2.5 8 2.5zM2.6 7h1.8a12 12 0 0 1 .8-3.9A5.5 5.5 0 0 0 2.6 7zm0 2a5.5 5.5 0 0 0 2.6 3.9A12 12 0 0 1 4.4 9zm3.2 0h4.4c-.3 2.7-1.3 4.5-2.2 4.5S6.1 11.7 5.8 9zm5.8 0a12 12 0 0 1-.8 3.9A5.5 5.5 0 0 0 13.4 9zm1.8-2a5.5 5.5 0 0 0-2.6-3.9c.4 1.1.7 2.4.8 3.9z"/></svg>
        </li>
      </ul>
    </div>
  </section>

</main>
</body>
</html>
```